Oriel Photography Business Card

I need a business card designed for a photography business based in Perth, Western Australia called Oriel Photography.

We specialise in wedding, event photography and portrait photography.

The business card must borrow the style of the attached logo.

The hex codes for the colours in the logo are:
#ED1D85 - Pink
#89C23E - Green
#37282F - Black

The name on the card will be:
Name: Tobrian
Phone: 0417395268
Website: www.orielphotography.example.com.au
Facebook: orielphotography

I am open and happy to accept creative concepts.

I’d like some space at the back for writing notes and appointment details.

```html
<!DOCTYPE html>
<html lang="en">
<head>
<meta charset="utf-8">
<title>Oriel Photography Business Card</title>
<link href="https://fonts.googleapis.com/css2?family=Open+Sans:ital,wght@0,400;0,600;0,700;1,400&family=Cinzel:wght@400&display=swap" rel="stylesheet">
<style>
  :root {
    --pink: #ED1D85;
    --green: #89C23E;
    --black: #37282F;
    --ink: #3c3c3c;
    --muted: #6b6b6b;
    --rule: #9a9a9a;
    --paper: #ffffff;
    --backdrop: #e6e6ec;
  }
  * { box-sizing: border-box; margin: 0; padding: 0; }
  html, body { width: 1200px; height: 987px; overflow: hidden; }
  body {
    background: var(--backdrop);
    font-family: "Open Sans", Arial, sans-serif;
    color: var(--ink);
    display: flex;
    align-items: center;
    justify-content: center;
    gap: 40px;
  }
  .card {
    position: relative;
    width: 560px;
    height: 342px;
    background: var(--paper);
    border-radius: 28px;
    overflow: hidden;
    box-shadow: 0 6px 18px rgba(0,0,0,.12);
  }

  /* Front */
  .front-band {
    position: absolute; left: 0; right: 0; bottom: 0; height: 92px;
    background: linear-gradient(100deg, var(--green) 0%, var(--green) 45%, var(--pink) 100%);
  }
  .brand-mark {
    position: absolute; left: 50%; top: 26px; transform: translateX(-50%);
    width: 40px; height: 40px; border-radius: 50%; background: var(--pink);
  }
  .brand-name {
    position: absolute; left: 0; right: 0; top: 80px; text-align: center;
    font-size: 17px; font-weight: 400; letter-spacing: 9px; text-transform: uppercase;
    color: var(--ink);
  }
  .contact { position: absolute; top: 128px; left: 40px; display: flex; gap: 18px; }
  .person { padding-right: 18px; border-right: 1px solid #cfcfcf; }
  .person-name { color: var(--pink); font-weight: 700; font-size: 21px; letter-spacing: .5px; }
  .phone { display: flex; align-items: center; gap: 6px; font-size: 14px; margin-top: 4px; }
  .phone svg { width: 14px; height: 14px; }
  .links { display: flex; flex-direction: column; gap: 8px; padding-top: 6px; font-size: 14px; }
  .link { display: flex; align-items: center; gap: 7px; }
  .link .square { width: 13px; height: 13px; background: var(--black); border-radius: 2px; }
  .link .dot { width: 13px; height: 13px; background: var(--green); border-radius: 50%; }

  /* Back */
  .back { padding: 26px 34px; }
  .back-title {
    font-family: "Cinzel", Georgia, serif; color: var(--pink);
    font-size: 17px; letter-spacing: 1px; margin-bottom: 14px;
  }
  .field { display: flex; align-items: flex-end; gap: 6px; font-size: 13px; margin-bottom: 12px; }
  .field .line { flex: 1; border-bottom: 1px solid var(--rule); height: 1px; }
  .field.narrow { width: 330px; }
  .next-row { display: flex; align-items: center; gap: 8px; font-size: 13px; margin-bottom: 14px; }
  .box { border: 1.3px solid #7a7a7a; border-radius: 3px; }
  .next-row .box { width: 86px; height: 22px; }
  .days { display: flex; align-items: center; gap: 6px; font-size: 11px; font-weight: 700; color: var(--muted); }
  .days .box { width: 24px; height: 20px; margin-right: 6px; }
  .note { font-style: italic; font-size: 12px; color: var(--muted); margin-top: 14px; }
  .back-brand {
    position: absolute; right: 30px; bottom: 30px; width: 130px;
    display: flex; flex-direction: column; align-items: center; gap: 8px;
  }
  .back-brand .mark { width: 52px; height: 52px; border-radius: 50%; background: var(--pink); }
  .back-brand .name { font-size: 12px; letter-spacing: 2px; text-transform: uppercase; text-align: center; color: var(--ink); }
</style>
</head>
<body>

  <section class="card front" aria-label="Business card front">
    <div class="front-band" role="img" aria-label="Decorative swoosh band in green, dark plum and pink"></div>
    <div class="brand-mark"></div>
    <div class="brand-name">Oriel Photography</div>
    <div class="contact">
      <div class="person">
        <div class="person-name">TOBRIAN</div>
        <div class="phone">
          <svg viewBox="0 0 14 14" aria-hidden="true"><circle cx="7" cy="7" r="7" fill="var(--green)"/><path d="M4.5,3.5 L6,3.5 L6.6,5.3 L5.7,6 C6.2,7.1 6.9,7.8 8,8.3 L8.7,7.4 L10.5,8 L10.5,9.5 C7,9.8 4.2,7 4.5,3.5 Z" fill="#fff"/></svg>
          0417395268
        </div>
      </div>
      <div class="links">
        <div class="link"><span class="square"></span>orielphotography</div>
        <div class="link"><span class="dot"></span>www.orielphotography.example.com.au</div>
      </div>
    </div>
  </section>

  <section class="card back" aria-label="Business card back">
    <h2 class="back-title">YOUR APPOINTMENT</h2>
    <div class="field narrow">Name :<span class="line"></span></div>
    <div class="field narrow">Date :<span class="line"></span></div>
    <div class="next-row">
      Next Appointment <span class="box"></span>
      Time : <span class="box"></span> am / pm
    </div>
    <div class="days">
      MON <span class="box"></span>
      TUE <span class="box"></span>
      WED <span class="box"></span>
      THU <span class="box"></span>
      FRI <span class="box"></span>
      SAT <span class="box"></span>
    </div>
    <p class="note">We appreciate a 24 hr. notice for cancellations</p>
    <div class="back-brand">
      <span class="mark"></span>
      <span class="name">Oriel Photography</span>
    </div>
  </section>

</body>
</html>
```